Business card design Needed for new logo / Construction business, home extensions and new builds

We need a business card design using our new logo files which i will attach to this project :)

We are a small construction business specialising in home extensions, new builds and property development. We are very ambitious and would appreciate professional and elegant designs for our new business card.

Very serious about using the services on MakerQuarry and recently acquired our new logo from here :)

Please get involved, i will feedback when i can as i am very busy but can respond daily, thanks

Target Market(s)

People that want to build onto their houses, new building developments or adding too their existing property

Industry/Entity Type

Construction

Contact Information for Business Card

Renwick Tolliver Construction, Lionel Ashby (Managing Director), Tel 07822254961, email - info@renwick-tolliver, www.renwick-tolliver.co.uk

Colors

Designer to choose colors to be used in the design.

Requirements
Must have
• I like a deep grey on the back please. A lot of you have provided black from and back, try mixing things up a little. The black looks cool 😎 Thanks

```html
<!DOCTYPE html>
<html lang="en">
<head>
<meta charset="utf-8">
<title>Renwick Tolliver Construction – Business Card</title>
<link href="https://fonts.googleapis.com/css2?family=Open+Sans:wght@400;600;700&display=swap" rel="stylesheet">
<style>
  :root {
    --stage: #2a2a2c;
    --card-black: #1d1d20;
    --card-grey: #6f7072;
    --emboss-dark: #151517;
    --emboss-grey: #5e5f61;
    --silver: #c9cacc;
    --silver-soft: #a9aaad;
    --gold: #d3a240;
    --gold-deep: #a77823;
    --white: #f1f1f1;
  }
  * { box-sizing: border-box; margin: 0; padding: 0; }
  html, body { width: 1200px; height: 780px; overflow: hidden; }
  body {
    background: var(--stage);
    font-family: "Open Sans", Arial, sans-serif;
    display: flex;
    align-items: center;
    justify-content: center;
    gap: 50px;
  }
  .card {
    position: relative;
    width: 525px;
    height: 300px;
    border-radius: 4px;
    overflow: hidden;
  }

  /* Front */
  .card--front { background: var(--card-black); }
  .front__watermark {
    position: absolute;
    left: 34px; top: 26px;
    width: 170px; height: 150px;
    background: var(--emboss-dark);
  }
  .front__brand {
    position: absolute;
    right: 34px; top: 30px;
    display: flex;
    align-items: center;
    gap: 10px;
    color: var(--silver);
    font-size: 13px;
    font-weight: 600;
    letter-spacing: 1.5px;
    text-transform: uppercase;
    text-align: right;
    line-height: 1.35;
  }
  .front__brand-mark {
    width: 30px; height: 30px;
    background: var(--gold);
    flex: none;
  }
  .front__person {
    position: absolute;
    right: 58px; top: 102px;
    text-align: right;
  }
  .front__name {
    font-size: 30px;
    font-weight: 700;
    line-height: 1.1;
  }
  .front__name-first { color: var(--silver); }
  .front__name-last { color: var(--gold); }
  .front__role {
    margin-top: 4px;
    color: var(--white);
    font-size: 14px;
    font-weight: 400;
    letter-spacing: 0.5px;
  }
  .front__contacts {
    position: absolute;
    right: 58px; top: 188px;
    list-style: none;
    text-align: right;
  }
  .front__contacts li {
    display: flex;
    justify-content: flex-end;
    align-items: center;
    gap: 10px;
    color: var(--white);
    font-size: 14px;
    line-height: 25px;
  }
  .front__contacts svg { width: 14px; height: 14px; flex: none; }
  .front__bars {
    position: absolute;
    right: 0; top: 150px;
    width: 22px; height: 80px;
    display: flex; flex-direction: column; gap: 3px;
  }
  .front__bars span {
    flex: 1;
    background: linear-gradient(90deg, var(--gold-deep), var(--gold), var(--gold-deep));
  }

  /* Back */
  .card--back {
    background: linear-gradient(135deg, #7a7b7d 0%, var(--card-grey) 55%, #5f6062 100%);
    display: flex;
    align-items: center;
    justify-content: center;
  }
  .back__brand {
    display: flex;
    align-items: center;
    gap: 14px;
    color: var(--emboss-grey);
    font-size: 18px;
    font-weight: 600;
    letter-spacing: 2px;
    text-transform: uppercase;
    line-height: 1.35;
  }
  .back__brand-mark {
    width: 40px; height: 40px;
    background: var(--emboss-grey);
    flex: none;
  }
</style>
</head>
<body>

  <section class="card card--front" aria-label="Business card front">
    <div class="front__watermark" aria-hidden="true"></div>

    <div class="front__brand">
      <span>Renwick Tolliver<br>Construction</span>
      <span class="front__brand-mark" aria-hidden="true"></span>
    </div>

    <div class="front__person">
      <h1 class="front__name"><span class="front__name-first">Lionel</span> <span class="front__name-last">Ashby</span></h1>
      <p class="front__role">Managing Director</p>
    </div>

    <ul class="front__contacts">
      <li>0782 225 4961
        <svg viewBox="0 0 24 24" aria-hidden="true"><path fill="#d3a240" d="M6.6 10.8a15.1 15.1 0 0 0 6.6 6.6l2.2-2.2a1 1 0 0 1 1-.25 11.4 11.4 0 0 0 3.6.57 1 1 0 0 1 1 1V20a1 1 0 0 1-1 1A17 17 0 0 1 3 4a1 1 0 0 1 1-1h3.5a1 1 0 0 1 1 1c0 1.25.2 2.45.57 3.57a1 1 0 0 1-.25 1z"/></svg>
      </li>
      <li>info@renwick-tolliver.co.uk
        <svg viewBox="0 0 24 24" aria-hidden="true"><rect x="2" y="5" width="20" height="14" rx="2" fill="#d3a240"/><path d="M3 6l9 7 9-7" fill="none" stroke="#1d1d20" stroke-width="1.8"/></svg>
      </li>
      <li>www.renwick-tolliver.co.uk
        <svg viewBox="0 0 24 24" aria-hidden="true"><circle cx="12" cy="12" r="10" fill="#d3a240"/><path d="M2 12h20M12 2c3 3 3 17 0 20M12 2c-3 3-3 17 0 20" fill="none" stroke="#1d1d20" stroke-width="1.4"/></svg>
      </li>
    </ul>

    <div class="front__bars" aria-hidden="true"><span></span><span></span><span></span><span></span></div>
  </section>

  <section class="card card--back" aria-label="Business card back">
    <div class="back__brand">
      <span class="back__brand-mark" aria-hidden="true"></span>
      <span>Renwick Tolliver<br>Construction</span>
    </div>
  </section>

</body>
</html>
```